Venture Capital Investment Firm

We are looking to overhaul our existing website (substantially), with only using the same logos (which we can provide).
We are an investment firm that focuses on making loans to late stage technology companies. Our site should ultimately look like other venture capital firms, and look modern and fresh. We have an existing website www.norvellhub.com which this will be replacing, although we will be using a lot of the existing written content, and potentially the numbers of pages we will need, we are not wed to anything else. Please feel free to shoot any questions at any time and thank you in advance for your help!
Websites we like as examples:
https://www.tesmarkfund.com/
https://www.brindlewoodpartners.com/
Target Market(s)
Potential investors who will invest in our firm, as well as potentially companies that are looking to borrow money from us.
Coding
Coded - Design and coding required
Number of Pages Required
5+ page
Colors
Designer to choose colors to be used in the design.
Look and feel

```html
<!DOCTYPE html>
<html lang="en">
<head>
<meta charset="utf-8">
<title>Norvell Capital — Structured Credit Investment</title>
<link href="https://fonts.googleapis.com/css2?family=Cinzel:wght@600;700&family=Oswald:wght@400;500&family=Poppins:wght@300;400;500&display=swap" rel="stylesheet">
<style>
:root{
  --navy:#0b0542;
  --purple:#4f40a3;
  --purple-soft:#6a5cb8;
  --lavender:#ebe9f5;
  --lavender-deep:#d9d5ee;
  --ink:#1c1a3a;
  --muted:#6d6b7e;
  --white:#ffffff;
}
*{margin:0;padding:0;box-sizing:border-box}
html,body{width:1200px;height:3599px;overflow:hidden}
body{position:relative;background:var(--white);font-family:"Poppins",sans-serif;color:var(--ink)}
.abs{position:absolute}
.bg-layer{position:absolute;left:0;top:0;width:1200px;height:3599px}
.brand{display:flex;align-items:center;gap:12px;font-family:"Cinzel",serif;font-weight:600;font-size:24px;letter-spacing:.5px;white-space:nowrap}
.brand .dot{width:28px;height:28px;border-radius:50%;border:3px solid currentColor}
.nav{left:524px;top:30px;font-size:13px;color:var(--white)}
.nav a{position:absolute;white-space:nowrap;text-decoration:none;color:var(--white);font-weight:400}
.nav a.active{color:#a79ce0}
.nav a.active::after{content:"";position:absolute;left:0;right:0;bottom:-9px;height:2px;background:#a79ce0}
.btn{display:flex;align-items:center;justify-content:center;background:var(--purple);color:var(--white);border-radius:28px;font-family:"Cinzel",serif;font-weight:700;letter-spacing:.5px;text-decoration:none;white-space:nowrap}
.btn-nav{left:993px;top:17px;width:127px;height:46px;font-family:"Poppins",sans-serif;font-weight:400;font-size:14px;background:var(--purple)}
.hero-title{left:80px;top:210px;font-family:"Oswald",sans-serif;font-weight:500;font-size:37px;line-height:47px;letter-spacing:-.2px;color:var(--white);text-transform:uppercase;white-space:nowrap}
.hero-sub{left:80px;top:366px;font-family:"Oswald",sans-serif;font-weight:400;font-size:17px;color:var(--white);letter-spacing:-.2px;white-space:nowrap}
.btn-hero{left:77px;top:411px;width:187px;height:54px;font-size:18px}
.photo{position:absolute;overflow:hidden}
.ph-meeting{left:566px;top:169px;width:233px;height:433px;border-radius:0 118px 118px 0;background:linear-gradient(135deg,#e8e4de,#9aa9bf 55%,#3c4d70)}
.ph-presenter{left:810px;top:212px;width:232px;height:433px;border-radius:0 0 118px 118px;background:linear-gradient(180deg,#d8dde6,#7b9fd0 60%,#4a78b9)}
.section-title{font-family:"Cinzel",serif;font-weight:700;color:var(--navy);text-align:center;text-transform:uppercase}
.center{left:0;width:1200px;text-align:center}
.idea-title{top:742px;font-size:40px;line-height:47px}
.idea-sub{top:843px;font-size:17px;color:var(--ink)}
.idea-body{left:320px;top:886px;width:560px;text-align:center;font-size:14.5px;line-height:27px;color:var(--muted);font-weight:300}
.btn-idea{left:511px;top:981px;width:178px;height:54px;font-size:18px}
.divider{left:80px;top:1102px;width:1043px;height:1px;background:#e7e6ee}
.strategy-title{top:1160px;font-size:40px}
.strategy-sub{top:1213px;font-size:17px}
.ph-life{left:138px;top:1356px;width:404px;height:333px;border-radius:0 90px 0 90px;background:linear-gradient(135deg,#2b3e5f,#6b8fbf 55%,#c9d7ea)}
.feat-title{font-family:"Cinzel",serif;font-weight:700;font-size:30px;color:var(--navy)}
.feat-body{font-size:14.5px;line-height:27px;color:var(--muted);font-weight:300}
.ph-tech{left:678px;top:1932px;width:402px;height:333px;border-radius:80px 0 80px 80px;background:linear-gradient(135deg,#6f8fb3,#3c5f8f 50%,#1f2e49)}
.news-title{left:80px;top:2366px;font-family:"Cinzel",serif;font-weight:700;font-size:40px;color:var(--navy)}
.news-sub{left:80px;top:2422px;font-size:16px}
.btn-more{left:957px;top:2376px;width:165px;height:55px;font-size:18px}
.card{position:absolute;top:2487px;width:245px;height:314px;border-radius:60px 0 60px 0;overflow:hidden;color:var(--white)}
.card .label{position:absolute;left:24px;bottom:26px;font-size:18px}
.card-1{left:80px;background:var(--purple)}
.card-1 .top{position:absolute;left:0;top:0;width:245px;height:212px;border-radius:0 0 60px 0;background:linear-gradient(180deg,#cfe7ef,#6ba7bf 60%,#2f6f88)}
.card-1 .label{left:18px;bottom:18px;font-size:15px;line-height:23px;width:210px}
.card-2{left:345px;background:linear-gradient(180deg,#5a6a8c,#2a2f5a 60%,var(--purple))}
.card-3{left:610px;background:linear-gradient(180deg,#8f8f97,#4a4a6a 60%,var(--purple))}
.card-4{left:876px;background:linear-gradient(180deg,#8aa0b8,#2a3a5c 55%,var(--purple))}
.nl-mark{left:582px;top:2871px;width:36px;height:36px;border-radius:50%;border:4px solid var(--navy)}
.nl-title{top:2947px;font-size:40px}
.nl-sub{top:2998px;font-size:16px}
.nl-form{left:279px;top:3050px;width:649px;height:54px;border-radius:28px;background:var(--white);box-shadow:0 4px 18px rgba(40,30,110,.08);display:flex;align-items:center}
.nl-form .field{padding-left:20px;font-size:14px;color:#9a98a8;flex:1}
.nl-form .btn{position:absolute;right:0;top:0;width:177px;height:54px;font-size:18px}
.foot-head{font-family:"Cinzel",serif;font-weight:700;font-size:19px;color:var(--white)}
.sitemap{left:80px;top:3289px;list-style:none}
.sitemap li{height:31.3px;font-size:15px;color:var(--white);display:flex;align-items:center;gap:10px}
.sitemap li::before{content:"";width:6px;height:6px;border-radius:50%;background:#7d70cf}
.contact-row{left:316px;display:flex;gap:20px;color:var(--white);font-size:14.5px;line-height:22px;white-space:nowrap}
.contact-row svg{flex:none;margin-top:2px}
.foot-brand{left:822px;top:3346px;color:var(--navy);font-size:28px}
.foot-brand .dot{width:34px;height:34px}
.legal{left:926px;top:3420px;font-size:15px;color:var(--navy);text-decoration:underline}
.foot-rule{left:80px;top:3534px;width:685px;height:1px;background:rgba(255,255,255,.25)}
.copyright{left:80px;top:3559px;font-size:14.5px;color:var(--white)}
</style>
</head>
<body>

<svg class="bg-layer" viewBox="0 0 1200 3599" aria-hidden="true">
  <defs>
    <linearGradient id="heroRight" x1="0" y1="0" x2="1" y2="0">
      <stop offset="0" stop-color="#ffffff"/>
      <stop offset="1" stop-color="#d9d5ee"/>
    </linearGradient>
    <linearGradient id="footRight" x1="0" y1="0" x2="1" y2="1">
      <stop offset="0" stop-color="#ffffff"/>
      <stop offset="1" stop-color="#d7d2ee"/>
    </linearGradient>
  </defs>
  <rect x="0" y="0" width="1200" height="680" fill="url(#heroRight)"/>
  <path d="M0,0 H790 C840,140 830,420 700,560 C590,680 380,700 220,640 C110,600 40,540 0,470 Z" fill="#0b0542"/>
  <path d="M0,0 H405 C410,120 360,260 230,330 C150,372 60,360 0,330 Z" fill="#5a4bb0"/>
  <path d="M826,266 A118,118 0 0 0 590,240" fill="none" stroke="#4f40a3" stroke-width="2.5"/>
  <path d="M838,244 H1070 V560 A116,116 0 0 1 838,560" fill="none" stroke="#4f40a3" stroke-width="2.5"/>
  <circle cx="471" cy="152" r="13" fill="none" stroke="#3a3380" stroke-width="2.5"/>
  <circle cx="293" cy="576" r="18" fill="none" stroke="#3a3380" stroke-width="3"/>
  <circle cx="506" cy="437" r="9" fill="none" stroke="#3a3380" stroke-width="2"/>
  <circle cx="89" cy="479" r="9" fill="none" stroke="#3a3380" stroke-width="2"/>
  <circle cx="1166" cy="417" r="10" fill="none" stroke="#4f40a3" stroke-width="3"/>

  <circle cx="77" cy="1523" r="300" fill="#ebe9f5"/>
  <circle cx="1118" cy="2040" r="240" fill="#ebe9f5"/>
  <circle cx="77" cy="2473" r="168" fill="#ebe9f5"/>
  <circle cx="1078" cy="1182" r="10" fill="none" stroke="#d9d5ee" stroke-width="2.5"/>
  <circle cx="649" cy="1357" r="9" fill="none" stroke="#d9d5ee" stroke-width="2.5"/>
  <circle cx="1076" cy="1660" r="16" fill="none" stroke="#d9d5ee" stroke-width="3"/>
  <circle cx="546" cy="1748" r="13" fill="none" stroke="#d9d5ee" stroke-width="3"/>
  <circle cx="426" cy="1926" r="16" fill="none" stroke="#d9d5ee" stroke-width="3"/>
  <circle cx="105" cy="2089" r="9" fill="none" stroke="#d9d5ee" stroke-width="2.5"/>
  <circle cx="418" cy="2246" r="9" fill="none" stroke="#d9d5ee" stroke-width="2.5"/>
  <circle cx="253" cy="2917" r="10" fill="none" stroke="#d9d5ee" stroke-width="2.5"/>
  <circle cx="1012" cy="2908" r="9" fill="none" stroke="#d9d5ee" stroke-width="2.5"/>

  <rect x="0" y="3120" width="1200" height="479" fill="url(#footRight)"/>
  <circle cx="994" cy="3194" r="16" fill="none" stroke="#d9d5ee" stroke-width="3"/>
  <path d="M0,3232 C180,3180 420,3150 560,3200 C720,3258 800,3420 850,3599 H0 Z" fill="#0b0542"/>
  <path d="M0,3420 C150,3420 300,3500 360,3599 H0 Z" fill="#3d2f8f" opacity=".55"/>
</svg>

<header>
  <div class="abs brand" style="left:77px;top:22px;color:var(--white)"><span class="dot"></span>Norvell Capital</div>
  <nav class="abs nav">
    <a class="active" style="left:0">HOME</a>
    <a style="left:66px">STRATEGY</a>
    <a style="left:161px">ABOUT US</a>
    <a style="left:258px">TEAM</a>
    <a style="left:318px">NEWS</a>
    <a style="left:377px">CONTACT</a>
  </nav>
  <a class="abs btn btn-nav">INVESTORS</a>
</header>

<section class="hero">
  <h1 class="abs hero-title">We are a global structured<br>credit investment firm<br>focused on the</h1>
  <p class="abs hero-sub">HEALTHCARE AND TECHNOLOGY INDUSTRIES</p>
  <a class="abs btn btn-hero">CONTACT US</a>
  <div class="photo ph-meeting" role="img" aria-label="Photo of colleagues seated at a meeting table"></div>
  <div class="photo ph-presenter" role="img" aria-label="Photo of a presenter pointing at charts on a screen"></div>
</section>

<section class="idea">
  <h2 class="abs center section-title idea-title">Norvell Capital started with<br>a big idea</h2>
  <p class="abs center idea-sub">Finance Proven Innovation With A Different Approach</p>
  <p class="abs idea-body">Norvell Capital is a private investment firm unique in its dual focus on life science and technology credit opportunit- ies.&nbsp; Our ambidextrous approach to investing reflects a broad recognition and appreciation for.</p>
  <a class="abs btn btn-idea">LEARN MORE</a>
</section>

<div class="abs divider"></div>

<section class="strategy">
  <h2 class="abs center section-title strategy-title">Strategy</h2>
  <p class="abs center strategy-sub">Partners For Growth Innovative Companies &amp; Their Investors</p>

  <div class="photo ph-life" role="img" aria-label="Illustration of a person using a VR headset beside a holographic body scan"></div>
  <h3 class="abs feat-title" style="left:615px;top:1429px">LIFE SCIENCES</h3>
  <p class="abs feat-body" style="left:617px;top:1482px;width:360px">We have a long track record of partnering with companies and investors that create and commercialize life science products, with extensive experience</p>
  <a class="abs btn" style="left:619px;top:1607px;width:176px;height:54px;font-size:18px">LEARN MORE</a>

  <h3 class="abs feat-title" style="left:205px;top:1969px">TECHNOLOGY</h3>
  <p class="abs feat-body" style="left:207px;top:2022px;width:360px">We uniquely offer sizeable and flexible structured credit financing solutions to innovative technology companies, with a focus on enterprise software</p>
  <a class="abs btn" style="left:210px;top:2147px;width:176px;height:55px;font-size:18px">LEARN MORE</a>
  <div class="photo ph-tech" role="img" aria-label="Photo of analysts reviewing a data dashboard on a monitor"></div>
</section>

<section class="news">
  <h2 class="abs news-title">LATEST NEWS</h2>
  <p class="abs news-sub">Press Release</p>
  <a class="abs btn btn-more">VIEW MORE</a>

  <article class="card card-1">
    <div class="top" role="img" aria-label="Photo of stacked coins with a rising chart"></div>
    <p class="label">Norvell Capital completes structured debt investment in BrightLedger</p>
  </article>
  <article class="card card-2" role="img" aria-label="Photo of hands holding a tablet with digital icons"><p class="label">Portfolio News</p></article>
  <article class="card card-3" role="img" aria-label="Photo of two business professionals"><p class="label">Press Release</p></article>
  <article class="card card-4" role="img" aria-label="Photo of a glossy dollar sign"><p class="label">Portfolio News</p></article>
</section>

<section class="newsletter">
  <div class="abs nl-mark"></div>
  <h2 class="abs center section-title nl-title">Sign up for newsletter</h2>
  <p class="abs center nl-sub">Would you like to receive our exclusive news for signup our newsletter !</p>
  <div class="abs nl-form">
    <span class="field">Enter Email *</span>
    <a class="btn">LEARN MORE</a>
  </div>
</section>

<footer>
  <h4 class="abs foot-head" style="left:80px;top:3249px">SITEMAP</h4>
  <ul class="abs sitemap">
    <li>Home</li><li>Strategy</li><li>About Us</li><li>Team</li><li>News</li><li>Contact</li><li>Investor</li>
  </ul>

  <h4 class="abs foot-head" style="left:316px;top:3249px">CONTACT US</h4>
  <div class="abs contact-row" style="top:3292px">
    <svg width="18" height="26" viewBox="0 0 18 26"><path d="M9,1 C4.5,1 1,4.5 1,9 C1,15 9,25 9,25 C9,25 17,15 17,9 C17,4.5 13.5,1 9,1 Z" fill="#7d70cf"/><circle cx="9" cy="9" r="3.2" fill="#0b0542"/></svg>
    <div style="margin-left:8px">SAN FRANCISCO<br>250 Harlow Street #310<br>San Francisco, CA&nbsp; 94107</div>
  </div>
  <div class="abs contact-row" style="top:3389px">
    <svg width="22" height="16" viewBox="0 0 22 16"><rect x="0" y="0" width="22" height="16" rx="2" fill="#7d70cf"/><path d="M1,1 L11,9 L21,1" fill="none" stroke="#0b0542" stroke-width="1.8"/></svg>
    <div style="margin-left:4px">GENERAL INQUIRIES : :<br>inquiries@norvellcap.com</div>
  </div>
  <div class="abs contact-row" style="top:3457px">
    <svg width="22" height="16" viewBox="0 0 22 16"><rect x="0" y="0" width="22" height="16" rx="2" fill="#7d70cf"/><path d="M1,1 L11,9 L21,1" fill="none" stroke="#0b0542" stroke-width="1.8"/></svg>
    <div style="margin-left:4px">MEDIA INQUIRIES :<br>media@norvellcap.com</div>
  </div>

  <div class="abs brand foot-brand"><span class="dot"></span>Norvell Capital</div>
  <a class="abs legal">Legal Disclaimer</a>

  <div class="abs foot-rule"></div>
  <p class="abs copyright">©2019 Norvell Capital Partners LLC.&nbsp; All Rights Reserved.</p>
</footer>

</body>
</html>
```